Large footwear retailer needs new powerpoint template

We are an Australian footwear retailer - Wombelle Kicks that needs a new powerpoint template. We want it to be fun and using our brand colours Teal and Black.
This will be used for multiple presentations so should include title slides, slides that allow us to high light our digital execution's, graphs, overviews and detail.
It can be bold and playful but also easy to use.
our website: https://www.wombellekicks.com.au/
Our Instagram: https://www.instagram.com/wombelle_trainers/

```html
<!DOCTYPE html>
<html lang="en">
<head>
<meta charset="utf-8">
<title>Wombelle Kicks — Presentation Template</title>
<link href="https://fonts.googleapis.com/css2?family=Montserrat:wght@400;500;600;700;800;900&display=swap" rel="stylesheet">
<style>
:root{
  --teal:#4aaba4;
  --teal-dark:#3a9d96;
  --teal-deep:#2f8781;
  --teal-light:#8fd3cd;
  --navy:#2c4763;
  --black:#111111;
  --ink:#222222;
  --white:#ffffff;
  --canvas:#7f7f7f;
  --card-line:#d9d9d9;
  --photo-grey:#e3e6e5;
  --star:#d8b400;
  --heart:#d9141f;
}
*{box-sizing:border-box;margin:0;padding:0}
html,body{width:1200px;height:3805px;overflow:hidden}
body{background:var(--canvas);font-family:"Montserrat",sans-serif;color:var(--ink);position:relative}
.slide{position:absolute;left:127px;width:946px;height:533px;background:var(--white);overflow:hidden;box-shadow:0 2px 6px rgba(0,0,0,.25)}
.slide--lined{border-bottom:4px solid var(--teal)}
.abs{position:absolute}
.brand{position:absolute;display:flex;align-items:center;gap:6px;font-weight:900;font-size:30px;letter-spacing:-.5px;color:var(--black);white-space:nowrap}
.brand__dot{width:30px;height:30px;border-radius:50%;border:5px solid var(--teal)}
.brand--white{color:var(--white)}
.brand--white .brand__dot{border-color:var(--white)}
.slide-title{position:absolute;left:53px;top:28px;font-weight:800;font-size:29px;color:var(--black);letter-spacing:.2px}
.photo{position:absolute}

/* title slide */
.hero__bg{left:0;top:0;width:946px;height:533px;
  background:
    radial-gradient(ellipse 320px 200px at 230px 60px,rgba(255,255,255,.16),transparent 70%),
    radial-gradient(ellipse 260px 220px at 820px 90px,rgba(20,80,78,.28),transparent 70%),
    linear-gradient(135deg,#5fb6af 0%,var(--teal) 55%,#3f9c96 100%)}
.hero__shoe{left:52px;top:198px;width:206px;height:92px;border-radius:50%;
  background:radial-gradient(ellipse at 50% 40%,rgba(255,255,255,.95) 0%,rgba(238,240,240,.85) 45%,rgba(255,255,255,0) 72%)}
.hero__circle{left:436px;top:56px;width:450px;height:450px;border-radius:50%;
  background:
    radial-gradient(circle at 62% 72%,rgba(255,255,255,.55) 0%,rgba(255,255,255,0) 28%),
    radial-gradient(circle at 40% 35%,#a7dcd7 0%,#6fb3bd 38%,#3f6f8a 72%,var(--navy) 100%);
  box-shadow:0 6px 20px rgba(0,0,0,.18)}
.hero__welcome{left:59px;top:337px;font-size:24px;font-weight:800;color:var(--black);letter-spacing:.5px}
.hero__name{left:57px;top:374px;font-size:36px;font-weight:900;color:var(--black);letter-spacing:-.5px;line-height:1.1;white-space:nowrap}
.socials{position:absolute;display:flex;gap:8px}
.socials span{width:36px;height:36px;border-radius:50%;border:2px solid var(--teal);position:relative}
.socials span::after{content:"";position:absolute;left:50%;top:50%;width:10px;height:10px;margin:-5px 0 0 -5px;border-radius:50%;background:var(--teal)}

/* digital executions */
.exec__title{left:0;width:946px;top:106px;text-align:center;font-size:29px;font-weight:800;color:var(--black)}
.cards{position:absolute;left:49px;top:169px;display:flex;gap:11px}
.card{width:205px;height:281px;border:1.5px solid var(--card-line);border-radius:8px;background:var(--white);position:relative;box-shadow:0 1px 4px rgba(0,0,0,.08)}
.card__photo{position:absolute;left:7px;top:7px;width:189px;height:118px;border-radius:6px}
.card__fav{position:absolute;right:14px;top:14px;width:14px;height:34px}
.card__stars{position:absolute;left:16px;top:147px;font-size:13px;color:var(--star);letter-spacing:1px}
.card__stars small{color:#b8a24a;font-size:10px;letter-spacing:0;margin-left:3px}
.card__brand{position:absolute;left:16px;top:170px;font-size:17px;font-weight:700;color:var(--black)}
.card__name{position:absolute;left:16px;top:203px;font-size:13.5px;color:#555}
.card__price{position:absolute;left:16px;top:229px;font-size:18px;font-weight:700;color:var(--teal-dark)}
.card__swatches{position:absolute;right:24px;top:235px;display:flex;gap:7px}
.card__swatches i{width:13px;height:13px;border-radius:50%;border:1.5px solid var(--black)}
.card__swatches i:first-child{background:var(--black)}
.pager{position:absolute;left:450px;top:481px;display:flex;gap:4px}
.pager i{width:9px;height:9px;border-radius:50%;background:var(--teal)}
.pager i.on{background:var(--black)}

/* overview */
.overview__frame{left:53px;top:138px;width:377px;height:336px;border:3px solid var(--teal);border-radius:10px}
.overview__photo{left:62px;top:129px;width:370px;height:330px;border-radius:8px;
  background:
    radial-gradient(ellipse 130px 170px at 210px 170px,rgba(236,226,234,.9),rgba(236,226,234,0) 70%),
    radial-gradient(ellipse 90px 60px at 180px 250px,rgba(60,170,150,.75),rgba(60,170,150,0) 70%),
    linear-gradient(90deg,#7467ad 0%,#7064a9 45%,#8f8dbd 62%,#b9c7d3 82%,#9fb9c9 100%)}
.overview__text{left:478px;top:133px;width:410px;font-size:13.6px;line-height:24.3px;text-align:justify;color:var(--ink)}

/* categories */
.category{position:absolute;top:122px;width:290px;text-align:center}
.category__photo{position:relative;margin:0 auto;width:246px;height:246px;border-radius:50%;box-shadow:0 3px 10px rgba(0,0,0,.15)}
.category__ring{position:absolute;inset:12px;border-radius:50%;border:2px dashed var(--white)}
.category__title{margin-top:27px;font-size:14.5px;font-weight:700;color:var(--black)}
.category__text{margin-top:6px;font-size:14.5px;line-height:18px;color:#333}
.category__link{display:inline-block;margin-top:12px;font-size:14px;font-weight:700;color:var(--teal-dark);text-decoration:underline}

/* graph */
.chart{left:61px;top:105px;width:825px;height:389px;border:1px solid #e2e2e2;box-shadow:0 1px 5px rgba(0,0,0,.12);background:var(--white)}
.chart text{font-family:"Montserrat",sans-serif}

/* thank you */
.thanks__bg{left:0;top:0;width:946px;height:533px;
  background:
    radial-gradient(ellipse 300px 260px at 470px 250px,rgba(255,255,255,.1),transparent 70%),
    linear-gradient(160deg,#55b0aa 0%,var(--teal) 50%,#44a39c 100%)}
.thanks__frame{left:69px;top:52px;width:809px;height:429px;border:1.5px solid var(--white);border-radius:12px}
.thanks__word{left:0;width:946px;top:226px;text-align:center;font-size:84px;font-weight:900;color:var(--white);letter-spacing:1px}
.socials--solid span{background:var(--white);border:none;width:34px;height:34px}
.socials--solid span::after{background:var(--teal)}
</style>
</head>
<body>

<section class="slide" style="top:118px">
  <div class="abs hero__bg photo" role="img" aria-label="Teal-tinted photo of sneakers on a street"></div>
  <svg class="abs" style="left:0;top:0" width="946" height="533" viewBox="0 0 946 533">
    <path d="M0 305 C120 250 260 225 380 270 C470 305 520 300 600 285 C720 262 840 270 946 300 L946 533 L0 533 Z" fill="#ffffff"/>
  </svg>
  <div class="photo hero__circle" role="img" aria-label="Circular photo of a walking sneaker on a kerb"></div>
  <div class="photo hero__shoe" role="img" aria-label="Pair of white court sneakers"></div>
  <div class="brand brand--white" style="left:53px;top:60px;font-size:34px"><span>WOMBELLE KICKS</span><span class="brand__dot"></span></div>
  <div class="abs hero__welcome">WELCOME TO</div>
  <div class="abs hero__name">WOMBELLE KICKS</div>
  <div class="socials" style="left:57px;top:451px"><span></span><span></span><span></span></div>
</section>

<section class="slide slide--lined" style="top:726px">
  <div class="brand" style="left:57px;top:28px"><span>WOMBELLE KICKS</span><span class="brand__dot"></span></div>
  <h2 class="abs exec__title">HIGHLIGHT OUR DIGITAL EXECUTIONS</h2>
  <div class="cards">
    <article class="card">
      <div class="card__photo" role="img" aria-label="Black running sneaker" style="background:radial-gradient(ellipse 70px 30px at 95px 62px,#2a2a2a,#2a2a2a 40%,rgba(42,42,42,0) 100%),var(--photo-grey)"></div>
      <svg class="card__fav" viewBox="0 0 14 34"><path d="M7 12 L1.5 6.5 A3 3 0 0 1 7 2.5 A3 3 0 0 1 12.5 6.5 Z" fill="var(--heart)"/><circle cx="7" cy="26" r="6" fill="#fff"/><path d="M7 22.5v7M3.5 26h7" stroke="#111" stroke-width="1.6"/></svg>
      <div class="card__stars">★★★★★<small>(0)</small></div>
      <div class="card__brand">STRIDER</div>
      <div class="card__name">Mens Aero Glide Run</div>
      <div class="card__price">$160.00</div>
      <div class="card__swatches"><i></i><i></i></div>
    </article>
    <article class="card">
      <div class="card__photo" role="img" aria-label="Cream sneaker with tan accents" style="background:radial-gradient(ellipse 70px 28px at 95px 62px,#efe2c4,#e8cf98 40%,rgba(232,207,152,0) 100%),#eeeceb"></div>
      <svg class="card__fav" viewBox="0 0 14 34"><path d="M7 12 L1.5 6.5 A3 3 0 0 1 7 2.5 A3 3 0 0 1 12.5 6.5 Z" fill="var(--heart)"/><circle cx="7" cy="26" r="6" fill="#fff"/><path d="M7 22.5v7M3.5 26h7" stroke="#111" stroke-width="1.6"/></svg>
      <div class="card__stars">★★★★★<small>(0)</small></div>
      <div class="card__brand">STRIDER</div>
      <div class="card__name">Womens Court Classic</div>
      <div class="card__price">$130.00</div>
      <div class="card__swatches"><i></i><i></i></div>
    </article>
    <article class="card">
      <div class="card__photo" role="img" aria-label="White sneaker with orange sole" style="background:radial-gradient(ellipse 70px 18px at 90px 78px,#f05a1e,rgba(240,90,30,0) 100%),radial-gradient(ellipse 72px 30px at 100px 58px,#fbfbfb,rgba(251,251,251,0) 100%),var(--photo-grey)"></div>
      <svg class="card__fav" viewBox="0 0 14 34"><path d="M7 12 L1.5 6.5 A3 3 0 0 1 7 2.5 A3 3 0 0 1 12.5 6.5 Z" fill="var(--heart)"/><circle cx="7" cy="26" r="6" fill="#fff"/><path d="M7 22.5v7M3.5 26h7" stroke="#111" stroke-width="1.6"/></svg>
      <div class="card__stars">★★★★★<small>(0)</small></div>
      <div class="card__brand">STRIDER</div>
      <div class="card__name">Womens Aero Glide Run</div>
      <div class="card__price">$160.00</div>
      <div class="card__swatches"><i></i><i></i></div>
    </article>
    <article class="card">
      <div class="card__photo" role="img" aria-label="White court sneaker with black stripe" style="background:radial-gradient(ellipse 75px 28px at 95px 62px,#fdfdfd,rgba(253,253,253,0) 100%),linear-gradient(180deg,#e6e9e8,#dcdfde)"></div>
      <svg class="card__fav" viewBox="0 0 14 34"><path d="M7 12 L1.5 6.5 A3 3 0 0 1 7 2.5 A3 3 0 0 1 12.5 6.5 Z" fill="var(--heart)"/><circle cx="7" cy="26" r="6" fill="#fff"/><path d="M7 22.5v7M3.5 26h7" stroke="#111" stroke-width="1.6"/></svg>
      <div class="card__stars">★★★★★<small>(0)</small></div>
      <div class="card__brand">STRIDER</div>
      <div class="card__name">Womens Court Classic</div>
      <div class="card__price">$160.00</div>
      <div class="card__swatches"><i></i><i></i></div>
    </article>
  </div>
  <div class="pager"><i></i><i class="on"></i><i></i></div>
</section>

<section class="slide slide--lined" style="top:1333px">
  <h2 class="slide-title">OVERVIEWS</h2>
  <div class="brand" style="right:62px;top:30px"><span>WOMBELLE KICKS</span><span class="brand__dot"></span></div>
  <div class="abs overview__frame"></div>
  <div class="photo overview__photo" role="img" aria-label="Teal and white sneakers against a purple brick wall"></div>
  <p class="abs overview__text">Since 1998 we've made it our business to deck out every single person who walks through our doors with the freshest footwear from all the biggest brands.But we reckon life goes beyond shoes. We believe it's what you do in them that truly counts.We're for the ones who dance harder, sing louder and don't care what anyone else thinks.Wombelle Kicks. GET YOUR KICKS! Since 1998 we've made it our business to deck out every single person who walks through our doors with the freshest footwear from all the biggest brands.But we reckon life goes beyond shoes. We believe it's what you do in them that truly counts.We're for the ones who dance harder, sing louder and don't care what anyone else thinks.</p>
</section>

<section class="slide slide--lined" style="top:1941px">
  <h2 class="slide-title">TRENDING CATEGORIES</h2>
  <div class="brand" style="right:62px;top:30px"><span>WOMBELLE KICKS</span><span class="brand__dot"></span></div>
  <div class="category" style="left:40px">
    <div class="category__photo" role="img" aria-label="Black knee-high boots" style="background:radial-gradient(ellipse 60px 100px at 45% 50%,#1b1b1b 0%,#2a2a2a 60%,rgba(42,42,42,0) 100%),linear-gradient(180deg,#e8e6e3 0%,#bfbfbf 45%,#3b4f86 62%,#d9d6d1 80%,#f1efec 100%)"><span class="category__ring"></span></div>
    <div class="category__title">STEP INTO ITNO</div>
    <p class="category__text">Lorem ipsum dolor sit amet<br>consectetur adipiscing elit</p>
    <a class="category__link">Shop Now</a>
  </div>
  <div class="category" style="left:328px">
    <div class="category__photo" role="img" aria-label="Tan lace-up boots against a blue wall" style="background:radial-gradient(ellipse 90px 45px at 50% 66%,#b8916a 0%,#c6a47c 45%,rgba(198,164,124,0) 100%),linear-gradient(180deg,#2838b8 0%,#2f45c2 55%,#b9bcc4 78%,#d9dadd 100%)"><span class="category__ring"></span></div>
    <div class="category__title">Book Up With Ridgeline</div>
    <p class="category__text">Lorem ipsum dolor sit amet<br>consectetur adipiscing elit</p>
    <a class="category__link">Shop Now</a>
  </div>
  <div class="category" style="left:615px">
    <div class="category__photo" role="img" aria-label="Black high-top canvas sneaker being laced" style="background:radial-gradient(ellipse 80px 55px at 58% 62%,#2b2b2b 0%,#1a1a1a 60%,rgba(26,26,26,0) 100%),radial-gradient(ellipse 60px 50px at 70% 20%,#e9e9e9,rgba(233,233,233,0) 100%),linear-gradient(180deg,#0c0c0c,#050505)"><span class="category__ring"></span></div>
    <div class="category__title">Trending Rn</div>
    <p class="category__text">Lorem ipsum dolor sit amet<br>consectetur adipiscing elit</p>
    <a class="category__link">Shop Now</a>
  </div>
</section>

<section class="slide" style="top:2548px">
  <h2 class="slide-title">GRAPHS</h2>
  <div class="brand" style="right:62px;top:30px"><span>WOMBELLE KICKS</span><span class="brand__dot"></span></div>
  <svg class="abs chart" width="825" height="389" viewBox="0 0 825 389">
    <g font-size="9.5" font-weight="600" fill="#222">
      <circle cx="30" cy="34" r="3.5" fill="#1a9634"/><text x="38" y="37.5">Lorem ipsum dolor</text>
      <circle cx="153" cy="34" r="3.5" fill="#c90015"/><text x="161" y="37.5">Lorem ipsum dolor</text>
      <circle cx="276" cy="34" r="3.5" fill="#a84ce6"/><text x="284" y="37.5">Lorem ipsum dolor</text>
      <circle cx="399" cy="34" r="3.5" fill="#e0a65a"/><text x="407" y="37.5">Lorem ipsum dolor</text>
      <circle cx="522" cy="34" r="3.5" fill="#29c5e6"/><text x="530" y="37.5">Lorem ipsum dolor</text>
    </g>
    <g font-size="8" fill="#333" text-anchor="end">
      <text x="28" y="98">100.0</text><text x="28" y="125">95.0</text><text x="28" y="153">90.0</text>
      <text x="28" y="180">85.0</text><text x="28" y="207">80.0</text><text x="28" y="235">75.0</text>
      <text x="28" y="262">70.0</text><text x="28" y="289">65.0</text><text x="28" y="317">60.0</text>
      <text x="28" y="344">55.0</text>
    </g>
    <g stroke="#d6d6d6" stroke-width="1">
      <line x1="123" y1="92" x2="123" y2="341"/><line x1="222" y1="92" x2="222" y2="341"/>
      <line x1="321" y1="92" x2="321" y2="341"/><line x1="420" y1="92" x2="420" y2="341"/>
      <line x1="519" y1="92" x2="519" y2="341"/><line x1="618" y1="92" x2="618" y2="341"/>
      <line x1="717" y1="92" x2="717" y2="341"/>
    </g>
    <line x1="32" y1="92" x2="32" y2="341" stroke="#999"/>
    <line x1="32" y1="341" x2="817" y2="341" stroke="#999"/>
    <rect x="41" y="284" width="64" height="57" fill="#29c5e6"/>
    <rect x="140" y="106" width="64" height="235" fill="#4aa8a3"/>
    <rect x="239" y="270" width="64" height="71" fill="#a84ce6"/>
    <rect x="338" y="210" width="64" height="131" fill="#1a9634"/>
    <rect x="437" y="319" width="64" height="22" fill="#e0a65a"/>
    <rect x="536" y="223" width="64" height="118" fill="#c90015"/>
    <rect x="635" y="163" width="64" height="178" fill="#4aa8a3"/>
    <rect x="734" y="207" width="64" height="134" fill="#29c5e6"/>
    <g font-size="8.5" fill="#333" text-anchor="middle">
      <text x="73" y="357">Lorem ipsum dolor</text><text x="172" y="357">Lorem ipsum dolor</text>
      <text x="271" y="357">Lorem ipsum dolor</text><text x="370" y="357">Lorem ipsum dolor</text>
      <text x="469" y="357">Lorem ipsum dolor</text><text x="568" y="357">Lorem ipsum dolor</text>
      <text x="667" y="357">Lorem ipsum dolor</text><text x="766" y="357">Lorem ipsum dolor</text>
    </g>
  </svg>
</section>

<section class="slide" style="top:3156px">
  <div class="abs thanks__bg photo" role="img" aria-label="Faint teal-tinted textured photo backdrop"></div>
  <div class="abs thanks__frame"></div>
  <div class="brand brand--white" style="left:0;width:946px;justify-content:center;top:160px;font-size:32px"><span>WOMBELLE KICKS</span><span class="brand__dot"></span></div>
  <h1 class="abs thanks__word">THANK YOU</h1>
  <div class="socials socials--solid" style="left:412px;top:350px"><span></span><span></span><span></span></div>
</section>

</body>
</html>
```